Flyer for Tallow Brisko - Design Agency

We need a 4-page square flyer measuring 14.8x14.8cm per page, to fold out, for a design agency targeting small businesses.
The design should be very modern. There shouldn't be too much content visible.
The background should be black. The color of the logo (attached) can also be used. The content is also attached and divided per page. We are open to alternative suggestions regarding the division.

```html
<!DOCTYPE html>
<html lang="de">
<head>
<meta charset="utf-8">
<title>Tallow Brisko – Flyer</title>
<link rel="stylesheet" href="https://fonts.googleapis.com/css2?family=Bungee&family=Montserrat:ital,wght@0,300;0,400;0,600;1,700;1,800&display=swap">
<style>
  :root{
    --stage:#c3f7fc;
    --navy:#1e1b4f;
    --navy-deep:#14133a;
    --teal:#8fd9d8;
    --purple:#9b5fb2;
    --pink:#c46a98;
    --blue:#2f3a9c;
    --white:#ffffff;
    --display:'Bungee', 'Arial Black', sans-serif;
    --text:'Montserrat', Arial, sans-serif;
  }
  *{margin:0;padding:0;box-sizing:border-box}
  html,body{width:960px;height:1200px;overflow:hidden}
  body{background:var(--stage);position:relative;font-family:var(--text);color:var(--white)}

  .spread{position:absolute;left:37px;width:886px;height:446px;display:flex;box-shadow:0 2px 6px rgba(0,0,0,.25)}
  .spread--outside{top:132px}
  .spread--inside{top:622px}
  .page{position:relative;width:443px;height:446px;overflow:hidden;
    background:linear-gradient(180deg,var(--navy-deep) 0%,var(--navy) 55%,var(--navy-deep) 100%)}
  .page--right{box-shadow:inset 6px 0 10px rgba(0,0,0,.35)}

  .decor{position:absolute}
  .decor--left-column{left:0;top:0;width:135px;height:446px;
    background:linear-gradient(180deg,#2b2f8a 0%,#3a2f8e 30%,#2c3c9e 60%,#3b2a7a 100%);opacity:.85;
    border-radius:0 60px 60px 0}
  .decor--right-column{right:0;top:0;width:105px;height:330px;
    background:linear-gradient(180deg,#5a3fa6 0%,#2c3ea0 45%,#7a4fb0 100%);opacity:.8;border-radius:50px 0 0 60px}
  .decor--top-band{left:0;top:0;width:443px;height:40px;
    background:linear-gradient(90deg,#3a2f7c,#2a4f8f 40%,#6a4a9e 80%,#b0679a);opacity:.75;border-radius:0 0 30px 30px}
  .decor--bottom-band{left:0;bottom:0;width:443px;height:150px;
    background:linear-gradient(90deg,#2c3a9a 0%,#4a3aa0 50%,#8a5aaa 100%);opacity:.75;border-radius:70px 70px 0 0}
  .decor--photo{left:40px;top:80px;width:400px;height:270px;
    background:radial-gradient(ellipse at 40% 50%,rgba(40,38,90,.8),rgba(20,19,58,0));}
  .decor--corner-br{right:0;bottom:0;width:70px;height:70px;border-radius:70px 0 0 0;
    background:linear-gradient(135deg,var(--purple),var(--pink));opacity:.85}
  .decor--corner-tl{left:0;top:0;width:60px;height:50px;border-radius:0 0 60px 0;
    background:linear-gradient(135deg,#3a2f8e,var(--purple));opacity:.8}

  .wordmark{position:absolute;font-family:var(--text);font-weight:600;color:var(--teal);line-height:.95;letter-spacing:-.02em}
  .wordmark--small{left:132px;top:185px;font-size:27px}
  .wordmark--large{left:70px;top:175px;font-size:50px}

  .tagline{position:absolute;left:132px;top:250px;font-family:var(--display);font-size:16px;line-height:18px}
  .cta{position:absolute;left:132px;top:296px;padding:3px 1px;white-space:nowrap;
    border-top:1px solid var(--teal);border-bottom:1px solid var(--teal);
    font-style:italic;font-weight:700;font-size:9.4px;line-height:12px;color:var(--teal)}
  .contact{position:absolute;left:132px;top:327px;list-style:none;font-size:10.5px;font-weight:300}
  .contact li{display:flex;gap:8px;align-items:flex-start;margin-bottom:12px;line-height:13px}
  .contact svg{flex:none;margin-top:1px}
  .owners{position:absolute;left:135px;top:410px;font-size:10px;font-weight:300}

  .headline{position:absolute;left:70px;top:304px;font-family:var(--display);font-size:31px;line-height:30px}

  .box{position:absolute;border:1px solid var(--teal)}
  .box-title{position:absolute;left:50%;transform:translateX(-50%);padding:0 9px;white-space:nowrap;
    font-family:var(--display);color:var(--teal);background:var(--navy)}
  .about{left:61px;top:133px;width:323px;height:122px}
  .about .box-title{top:-12px;font-size:17px}
  .about p{position:absolute;left:0;right:0;top:22px;text-align:center;font-weight:300;font-size:14px;line-height:17.6px}

  .services{left:15px;top:29px;width:409px;height:402px}
  .services .box-title{top:-12px;font-size:17px;background:var(--navy-deep)}
  .service{position:absolute;font-size:10.2px;font-weight:400;line-height:12.5px}
  .service .pill{display:inline-block;background:var(--purple);color:var(--teal);font-style:italic;font-weight:800;
    font-size:13.5px;line-height:15px;padding:0 7px;border-radius:8px}
  .service .icon{position:absolute;width:34px;height:34px;border-radius:50%;background:#efe9f3;border:3px solid var(--purple);
    display:flex;align-items:center;justify-content:center}
  .service--left{left:12px;padding-left:40px}
  .service--left .icon{left:0;top:0}
  .service--right{right:12px;padding-right:40px;text-align:right}
  .service--right .icon{right:0;top:0}

  .divider{position:absolute;left:190px;top:229px;width:30px;height:1px;background:var(--purple)}
  .why-title{position:absolute;left:0;right:0;top:240px;text-align:center;font-family:var(--display);color:var(--teal);font-size:17px}
  .reasons{position:absolute;left:13px;top:278px;list-style:none;font-size:10.2px;font-weight:400;line-height:14.5px}
  .reasons li{position:relative;padding-left:24px;margin-bottom:15px;width:360px}
  .reasons svg{position:absolute;left:0;top:6px}
</style>
</head>
<body>

<section class="spread spread--outside">
  <div class="page page--left page--back">
    <div class="decor decor--left-column" role="img" aria-label="Geometrische Formen in Blau und Violett"></div>
    <div class="wordmark wordmark--small">Tallow<br>Brisko</div>
    <div class="tagline">Designs, die wirken.<br>Marken, die bleiben.</div>
    <div class="cta">Kontaktiere uns für eine kostenlose Beratung!</div>
    <ul class="contact">
      <li><svg width="10" height="10" viewBox="0 0 10 10"><circle cx="5" cy="5" r="5" fill="var(--teal)"/><path d="M2.5 3.5h5v3h-5z M2.5 3.5l2.5 2 2.5-2" fill="none" stroke="var(--navy)" stroke-width=".8"/></svg>studio@tallowbrisko.de</li>
      <li><svg width="10" height="10" viewBox="0 0 10 10"><circle cx="5" cy="5" r="5" fill="var(--teal)"/><path d="M3.2 2.8c.3 2 1.8 3.6 3.8 4l.5-1-1-.6-.5.5C5 5.3 4.6 4.8 4.4 4.3l.5-.5-.6-1z" fill="var(--navy)"/></svg>+49 000 58213</li>
      <li><svg width="10" height="10" viewBox="0 0 10 10"><circle cx="5" cy="5" r="5" fill="var(--teal)"/><path d="M5 8C3.5 6 3 5 3 4a2 2 0 014 0c0 1-.5 2-2 4z" fill="var(--navy)"/></svg>Lindenweg 8<br>60311 Musterstadt</li>
    </ul>
    <div class="owners">Inhaber: Ilse Marow &amp; Jonas Feldt</div>
  </div>
  <div class="page page--right page--cover">
    <div class="decor decor--right-column" role="img" aria-label="Geometrische Formen in Blau und Violett"></div>
    <div class="wordmark wordmark--large">Tallow<br>Brisko</div>
    <div class="headline">Dein<br>Unternehmen.<br>Dein Stil.<br>Unser Design.</div>
  </div>
</section>

<section class="spread spread--inside">
  <div class="page page--left page--about">
    <div class="decor decor--photo" role="img" aria-label="Abgedunkeltes Foto eines Arbeitsplatzes"></div>
    <div class="decor decor--top-band" role="img" aria-label="Geometrische Formen in Blau und Violett"></div>
    <div class="decor decor--bottom-band" role="img" aria-label="Geometrische Formen in Blau und Violett"></div>
    <div class="box about">
      <h2 class="box-title">Modern, mutig, markant</h2>
      <p>Tallow Brisko gestaltet die<br>Zukunft deines Unternehmensauftritts<br>Wir machen aus Ideen visuelle<br>Erlebnisse und sorgen dafür,<br>dass deine Marke im Gedächtnis bleibt.</p>
    </div>
  </div>
  <div class="page page--right page--services">
    <div class="decor decor--corner-tl" role="img" aria-label="Geometrische Form in Violett"></div>
    <div class="decor decor--corner-br" role="img" aria-label="Geometrische Form in Violett und Rosa"></div>
    <div class="box services">
      <h2 class="box-title">Unsere Leistungen</h2>

      <div class="service service--left" style="top:27px">
        <span class="icon"><svg width="16" height="16" viewBox="0 0 16 16"><path d="M4 12l2-5 6-5-2 7z" fill="var(--purple)"/></svg></span>
        <span class="pill">Next-Level Flyer</span><br>
        Nicht nur Papier, sondern deine Botschaft im perfekten Look.
      </div>

      <div class="service service--right" style="top:72px">
        <span class="icon"><svg width="16" height="16" viewBox="0 0 16 16"><circle cx="8" cy="8" r="7" fill="var(--purple)"/><circle cx="5" cy="6" r="1.3" fill="#fff"/><circle cx="9" cy="4.5" r="1.3" fill="#fff"/><circle cx="11" cy="8" r="1.3" fill="#fff"/></svg></span>
        <span class="pill">Corporate Identity</span><br>
        Ein Design, das deine Marke spricht – individuell, stark,<br>unvergesslich.
      </div>

      <div class="service service--left" style="top:122px">
        <span class="icon"><svg width="16" height="16" viewBox="0 0 16 16"><rect x="2" y="3" width="12" height="8" fill="none" stroke="var(--purple)" stroke-width="1.4"/><path d="M6 14h4M8 11v3" stroke="var(--purple)" stroke-width="1.4"/></svg></span>
        <span class="pill">Digital &amp; Print</span><br>
        Ob Social Media Grafiken oder klassisches Printdesign – wir sind<br>da, wo du uns brauchst.
      </div>

      <div class="service service--right" style="top:175px">
        <span class="icon"><svg width="16" height="16" viewBox="0 0 16 16"><path d="M8 1l1.6 5.4L15 8l-5.4 1.6L8 15l-1.6-5.4L1 8l5.4-1.6z" fill="var(--purple)"/></svg></span>
        <span class="pill">Alles aus einer Hand</span><br>
        Logo, Farben, Typografie, Flyer und vieles mehr – wir bauen das<br>Fundament für deinen Erfolg.
      </div>

      <div class="divider"></div>
      <h2 class="why-title">Warum wir?</h2>
      <ul class="reasons">
        <li><svg width="12" height="16" viewBox="0 0 12 16"><path d="M1 1l10 7-10 7 3-7z" fill="var(--purple)"/></svg>Dein Style, unser Know-how: Wir kombinieren deine Vision mit moderner Ästhetik.</li>
        <li><svg width="12" height="16" viewBox="0 0 12 16"><path d="M1 1l10 7-10 7 3-7z" fill="var(--purple)"/></svg>Persönlicher Service – Wir hören zu und setzen um, was dich einzigartig macht</li>
        <li><svg width="12" height="16" viewBox="0 0 12 16" style="top:-1px"><path d="M1 1l10 7-10 7 3-7z" fill="var(--purple)"/></svg>Flexible Lösungen für die unterschiedlichsten Anforderungen</li>
      </ul>
    </div>
  </div>
</section>

</body>
</html>
```